Property management company looking for modern card design

We at Blue Heron Partners provides property management services for its residential and commercial properties, with expertise in all categories of multifamily, industrial and office projects throughout California.

We need a business card design that is professional and modern designed business card. In our field, clients get hundreds of business cards, we would like our card to stand out.

Please avoid small print.

Target Market(s)

Professionals and high end clients

Industry/Entity Type

Financial Planning

Contact Information for Business Card

Company Name: Blue Heron Partners, Name, email, license #, phone number, website blueheronpartners.com

Font styles to use
Sans Serif

Requirements
Must have
• The card design needs to be adaptable because there is a possibly we will be expanding into different sectors other than real estate. The card design should be focused on financial planning and asset management.
Nice to have
• Modern and simple business card. Eye catching. Non-standard size/shaped cards would be great.
• blueheronpartners.com
Should not have
• Too many bright color or any pictures or shapes of real estate stuff.

```html
<!DOCTYPE html>
<html lang="en">
<head>
<meta charset="utf-8">
<title>Blue Heron Partners – Business Card</title>
<link href="https://fonts.googleapis.com/css2?family=Open+Sans:wght@400;600;700&display=swap" rel="stylesheet">
<style>
  :root {
    --stage-top: #2c2c2c;
    --stage-bottom: #050505;
    --card-red-glow: #f0283a;
    --card-red: #c8141f;
    --card-red-deep: #7d1016;
    --brand-red: #b3121c;
    --white: #ffffff;
    --rule-grey: #8a8a8a;
  }
  * { margin: 0; padding: 0; box-sizing: border-box; }
  html, body { width: 1200px; height: 900px; overflow: hidden; }
  body {
    position: relative;
    background: radial-gradient(ellipse 120% 90% at 50% 10%, var(--stage-top) 0%, #161616 55%, var(--stage-bottom) 100%);
    font-family: "Open Sans", Arial, sans-serif;
  }
  .card {
    position: absolute;
    top: 306px;
    height: 271px;
    border-radius: 10px;
    overflow: hidden;
  }
  .card--front {
    left: 150px;
    width: 438px;
    background: radial-gradient(ellipse 65% 85% at 48% 42%, var(--card-red-glow) 0%, var(--card-red) 45%, var(--card-red-deep) 100%);
    color: var(--white);
  }
  .brand-disc {
    position: absolute;
    left: 51px;
    top: 66px;
    width: 138px;
    height: 138px;
    border-radius: 50%;
    background: var(--white);
    display: flex;
    align-items: center;
    justify-content: center;
    text-align: center;
    padding: 0 18px;
    color: var(--brand-red);
    font-weight: 600;
    font-size: 16px;
    line-height: 1.25;
  }
  .details {
    position: absolute;
    left: 227px;
    top: 70px;
  }
  .details__name { font-size: 14px; font-weight: 700; line-height: 18px; }
  .details__role { font-size: 11.5px; font-weight: 400; line-height: 15px; }
  .details__license { margin-top: 22px; font-size: 12px; line-height: 16px; }
  .details__license strong { font-weight: 700; }
  .contact { list-style: none; margin-top: 11px; }
  .contact__item {
    display: flex;
    align-items: center;
    gap: 6px;
    font-size: 11.5px;
    line-height: 16px;
  }
  .contact__icon { width: 9px; height: 9px; flex: none; fill: var(--white); }

  .card--back {
    left: 608px;
    width: 440px;
    background: var(--white);
  }
  .wordmark {
    position: absolute;
    left: 0;
    right: 0;
    top: 86px;
    text-align: center;
    color: var(--brand-red);
    font-weight: 400;
    font-size: 38px;
    letter-spacing: 0.5px;
  }
  .wordmark-rule {
    position: absolute;
    top: 167px;
    left: 41px;
    width: 358px;
    height: 1px;
    background: var(--rule-grey);
  }
</style>
</head>
<body>
  <section class="card card--front" aria-label="Business card front">
    <div class="brand-disc">Blue Heron Partners</div>
    <div class="details">
      <p class="details__name">Daniel Whitford</p>
      <p class="details__role">Managing Director</p>
      <p class="details__license"><strong>License:</strong> BHP01245</p>
      <ul class="contact">
        <li class="contact__item">
          <svg class="contact__icon" viewBox="0 0 10 10" aria-hidden="true"><path d="M2.2 0.5 L3.6 2.6 L2.7 3.6 C3.3 4.9 4.9 6.6 6.4 7.3 L7.4 6.4 L9.5 7.8 L8.5 9.4 C5 9.2 0.8 5 0.6 1.5 Z"/></svg>
          <span>044-987 654 321</span>
        </li>
        <li class="contact__item">
          <svg class="contact__icon" viewBox="0 0 10 10" aria-hidden="true"><path d="M0.5 2 H9.5 V8 H0.5 Z M0.5 2 L5 5.4 L9.5 2" stroke="#c8141f" stroke-width="0.8"/></svg>
          <span>hello@blueheronpartners.com</span>
        </li>
        <li class="contact__item">
          <svg class="contact__icon" viewBox="0 0 10 10" aria-hidden="true"><circle cx="5" cy="5" r="4.5"/></svg>
          <span>www.blueheronpartners.com</span>
        </li>
      </ul>
    </div>
  </section>

  <section class="card card--back" aria-label="Business card back">
    <p class="wordmark">Blue Heron Partners</p>
    <div class="wordmark-rule"></div>
  </section>
</body>
</html>
```